Fitness Business Card Design Needed

We are looking for a business card design that stands out but is also simple and unique. I like the idea of on one side using the picture of myself with my logo at my feet. I love the texture on the business card so please take that into account when designing. Then on the other side having my contact details. I want it to be clean, modern, and pretty. I am open to designs that allow spot gloss or gold foiling.

Contact Information for Business Card

Space for Name, Phone number, email, and website

```html
<!DOCTYPE html>
<html lang="en">
<head>
<meta charset="utf-8">
<title>PetitePower Fitness – Business Card</title>
<link rel="stylesheet" href="https://fonts.googleapis.com/css2?family=Roboto:wght@300;400;500&display=swap">
<style>
  :root {
    --backdrop: #2b2b2b;
    --card: #ffffff;
    --ink: #2f2f2f;
    --gold: #b88a3e;
    --sand-light: #f3e6da;
    --skin: #d9926f;
    --suit: #d9483a;
  }
  * { box-sizing: border-box; margin: 0; padding: 0; }
  html, body {
    width: 1200px; height: 801px; overflow: hidden;
    background: var(--backdrop);
    font-family: "Roboto", Arial, sans-serif;
    color: var(--ink);
  }
  .stage { position: relative; width: 1200px; height: 801px; }
  .card {
    position: absolute;
    width: 600px; height: 343px;
    background: var(--card);
    box-shadow: 0 6px 18px rgba(0,0,0,0.35);
  }
  .card--contact { left: 540px; top: 50px; }
  .card--brand { left: 70px; top: 410px; }

  .brand-name {
    font-weight: 300;
    letter-spacing: 4px;
    color: var(--ink);
    white-space: nowrap;
    display: flex; align-items: center; gap: 10px;
  }
  .brand-name__square { width: 10px; height: 10px; background: var(--gold); display: inline-block; }

  .card--contact .brand-name { position: absolute; left: 44px; top: 50px; font-size: 19px; }

  .person { position: absolute; left: 44px; top: 140px; }
  .person__name { color: var(--gold); font-weight: 500; font-size: 25px; letter-spacing: 0.5px; }
  .person__title { font-size: 15px; margin-top: 2px; letter-spacing: 0.3px; }
  .person__address { font-size: 14px; line-height: 19px; margin-top: 12px; }

  .contact-list { list-style: none; margin-top: 12px; font-size: 14px; line-height: 20px; }
  .contact-list li { display: flex; align-items: center; gap: 8px; }
  .contact-list svg { width: 12px; height: 12px; fill: var(--gold); flex: none; }

  .portrait {
    position: absolute; right: 40px; top: 40px;
    width: 160px; height: 275px;
    background: linear-gradient(180deg, #e9d8c6 0%, var(--skin) 35%, var(--suit) 50%, var(--skin) 65%, var(--sand-light) 100%);
    border-radius: 80px 80px 6px 6px;
    opacity: 0.85;
  }

  .card--brand .brand-name {
    position: absolute; left: 50%; top: 200px; transform: translateX(-50%);
    font-size: 22px;
  }
</style>
</head>
<body>
<main class="stage">
  <section class="card card--contact" aria-label="Card front with contact details">
    <div class="brand-name"><span class="brand-name__square"></span>PETITEPOWER FITNESS</div>
    <div class="person">
      <h1 class="person__name">DANA RUIZ</h1>
      <p class="person__title">FITNESS TRAINER</p>
      <p class="person__address">1420 Willow Court<br>Juneau, Alaska 39812</p>
      <ul class="contact-list">
        <li><svg viewBox="0 0 24 24" aria-hidden="true"><path d="M6.6 10.8a15.1 15.1 0 0 0 6.6 6.6l2.2-2.2c.3-.3.7-.4 1-.2 1.1.4 2.3.6 3.6.6.6 0 1 .4 1 1V20c0 .6-.4 1-1 1A17 17 0 0 1 3 4c0-.6.4-1 1-1h3.5c.6 0 1 .4 1 1 0 1.3.2 2.5.6 3.6.1.3 0 .7-.2 1z"/></svg>555 014 2278</li>
        <li><svg viewBox="0 0 24 24" aria-hidden="true"><path d="M2 5h20v14H2zM4 7v.5l8 5 8-5V7l-8 5z"/></svg>info@petitepower.com</li>
        <li><svg viewBox="0 0 24 24" aria-hidden="true"><circle cx="12" cy="12" r="10"/></svg>www.petitepower.com</li>
      </ul>
    </div>
    <div class="portrait" role="img" aria-label="Full-length photo of the trainer in a red swimsuit standing on sand"></div>
  </section>

  <section class="card card--brand" aria-label="Card back with brand name">
    <div class="brand-name"><span class="brand-name__square"></span>PETITEPOWER FITNESS</div>
  </section>
</main>
</body>
</html>
```